Norrell Advisory WA Business Card

Create an interesting, eye catching and colourful two sided business card. We are a business consulting operation assisting SME's improve all areas of their business. We provide consulting services to assist SME's to create a culture of continuous improvement, making a positive difference in the business. Our tag line is Small changes, big rewards. We want to create a well recognised, innovative brand that can be continued throughout our website, social media and email correspondence.

Target Market(s)

Small to Medium Enterprise Business Owners

Industry/Entity Type

Business Consultant

Contact Information for Business Card

Name of Business: Norrell Advisory - Small Steps Lasting Gains
Derek Holloway Ph 0407385510 Megan Holloway Ph 0407913847
Email norrelladvisorywa@mailbox-example.com
Web address TBA
FaceBook page TBA

BACKSIDE OF CARD

Providing assistance with:

• Organisation & Efficiency
• Revenue generation & Marketing
• Financial Management
• Production quality & delivery
• Systems & Process documentation
• Exit Strategy

Font styles to use
Other font styles liked:
• Calibri

Colors

Designer to choose colors to be used in the design.

Requirements
Must have
• Calibri font

```html
<!DOCTYPE html>
<html lang="en">
<head>
<meta charset="utf-8">
<title>Norrell Advisory WA – Business Card</title>
<link rel="stylesheet" href="https://fonts.googleapis.com/css2?family=Open+Sans:ital,wght@0,400;0,600;0,700;1,700&display=swap">
<style>
  :root {
    --page-bg: #e4e4e4;
    --card-light: #ffffff;
    --card-dark-1: #2a2a2a;
    --card-dark-2: #161616;
    --ink: #4d4d4d;
    --ink-soft: #555555;
    --brand-ink: #2f2f2f;
    --rule: #8a8a8a;
    --back-ink: #e6e6e6;
    --back-rule: #9a9a9a;
    --mark: #2e9fd8;
    --icon: #4a4a4a;
  }
  * { box-sizing: border-box; margin: 0; padding: 0; }
  html, body {
    width: 1125px; height: 1200px; overflow: hidden;
    background: var(--page-bg);
    font-family: "Open Sans", Arial, sans-serif;
  }
  .card {
    position: absolute; left: 171px; width: 826px; height: 471px;
    box-shadow: 0 2px 5px rgba(0,0,0,.25);
  }
  .card--front { top: 106px; background: var(--card-light); }
  .card--back {
    top: 639px;
    background: radial-gradient(ellipse at 70% 30%, var(--card-dark-1), var(--card-dark-2));
  }
  .abs { position: absolute; white-space: nowrap; }

  /* front: brand block */
  .brand-square {
    left: 171px; top: 142px; width: 100px; height: 100px;
    background: var(--mark);
  }
  .brand-name {
    left: 36px; width: 370px; text-align: center; top: 296px;
    font-weight: 700; font-size: 29px; letter-spacing: .2px; color: var(--brand-ink);
    line-height: 1.2;
  }
  .brand-tagline {
    left: 36px; width: 370px; text-align: center; top: 333px;
    font-weight: 600; font-size: 12.5px; letter-spacing: 3.6px; color: var(--ink-soft);
    line-height: 1.2;
  }
  .divider {
    left: 413px; top: 123px; width: 1px; height: 225px; background: var(--rule);
  }

  /* front: people and contacts */
  .person-name { left: 451px; font-weight: 600; font-size: 33px; color: var(--ink); line-height: 1; }
  .person-phone { left: 453px; font-weight: 700; font-size: 24px; color: var(--ink); line-height: 1; }
  .person-name--first { top: 120px; }
  .person-phone--first { top: 156px; }
  .person-name--second { top: 193px; }
  .person-phone--second { top: 230px; }

  .contact { left: 455px; display: flex; align-items: center; gap: 10px;
    font-size: 16.5px; color: var(--ink-soft); line-height: 1; }
  .contact svg { width: 16px; height: 16px; flex: none; }
  .contact--social { top: 267px; }
  .contact--email { top: 292px; }
  .contact--web { top: 317px; }

  /* back */
  .back-square {
    left: 353px; top: 105px; width: 120px; height: 120px; background: var(--mark);
  }
  .back-name {
    left: 0; width: 826px; text-align: center; top: 240px;
    font-weight: 700; font-size: 30px; color: var(--back-ink); line-height: 1.2;
  }
  .services-heading {
    left: 0; width: 826px; top: 345px; text-align: center;
    font-style: italic; font-weight: 700; font-size: 26.5px; color: var(--back-ink);
    line-height: 1.2;
  }
  .services-rule { top: 363px; height: 1px; width: 181px; background: var(--back-rule); }
  .services-rule--left { left: 61px; }
  .services-rule--right { left: 584px; }
  .services-line {
    left: 0; width: 826px; text-align: center;
    font-size: 18px; color: var(--back-ink); line-height: 1.2;
  }
  .services-line--one { top: 383px; }
  .services-line--two { top: 408px; }
  .bullet { margin: 0 3px; }
</style>
</head>
<body>

<section class="card card--front" aria-label="Business card front">
  <div class="abs brand-square" aria-hidden="true"></div>
  <div class="abs brand-name">NORRELL ADVISORY</div>
  <div class="abs brand-tagline">SMALL STEPS LASTING GAINS</div>
  <div class="abs divider"></div>

  <div class="abs person-name person-name--first">DEREK HOLLOWAY</div>
  <div class="abs person-phone person-phone--first">0407385510</div>
  <div class="abs person-name person-name--second">MEGAN HOLLOWAY</div>
  <div class="abs person-phone person-phone--second">0407913847</div>

  <div class="abs contact contact--social">
    <svg viewBox="0 0 17 17" aria-hidden="true"><rect x="1" y="1" width="15" height="15" fill="var(--icon)"/></svg>
    <span>norrelladvisorywa</span>
  </div>
  <div class="abs contact contact--email">
    <svg viewBox="0 0 17 17" aria-hidden="true">
      <rect x="1" y="3.5" width="15" height="10" fill="var(--icon)"/>
      <path d="M1.5 4 L8.5 9.5 L15.5 4" fill="none" stroke="#fff" stroke-width="1.3"/>
    </svg>
    <span>norrelladvisorywa@mailbox-example.com</span>
  </div>
  <div class="abs contact contact--web">
    <svg viewBox="0 0 17 17" aria-hidden="true">
      <circle cx="8.5" cy="8.5" r="7.5" fill="var(--icon)"/>
      <ellipse cx="8.5" cy="8.5" rx="3" ry="7.5" fill="none" stroke="#fff" stroke-width="1"/>
      <line x1="1" y1="8.5" x2="16" y2="8.5" stroke="#fff" stroke-width="1"/>
    </svg>
    <span>www.norrelladvisorywa.com</span>
  </div>
</section>

<section class="card card--back" aria-label="Business card back">
  <div class="abs back-square" aria-hidden="true"></div>
  <div class="abs back-name">NORRELL ADVISORY</div>

  <div class="abs services-rule services-rule--left"></div>
  <div class="abs services-heading">Providing assistance with</div>
  <div class="abs services-rule services-rule--right"></div>

  <div class="abs services-line services-line--one">Organisation &amp; Efficiency<span class="bullet">•</span>Revenue generation &amp; Marketing<span class="bullet">•</span>Financial Management</div>
  <div class="abs services-line services-line--two">Production quality &amp; delivery<span class="bullet">•</span>Systems &amp; Process documentation<span class="bullet">•</span>Exit Strategy</div>
</section>

</body>
</html>
```